Australian Trucking Company Requires Professional Looking Stationary

We require a professional looking stationary design that incorporates our newly designed logo.

Our business, called "Brell Haulage Contracting", provides contracting work, transport and logistics to business in Western Australia particularly with links to the mining sector.

We are a small business looking to expand and our new logo and our new stationary will help develop our brand image in our market place.

Target Market(s)

Businesses and Corporation with links to the Mining Sector

Industry/Entity Type

Small Business

Requirements
Must have
• The letterhead must have the following details:
The new logo

Text saying: "Brell Holdings Pty Ltd (ACN 582 316 907) ATF The Brell Discretionary Trust T/AS"
"ABN 71 834 209 553"
Address "P.O Box 817 Wattlegrove WA, 6958"
Phone: 08 9352 7140
Email: brellhaul@mailbox-example.com.au

The text on the letterhead should be editable as the details are likely to change in the near future. Provision should be made for a website address all though one isn't available at the moment.

The styling, layout and font text is entirely up to the designer.

```html
<!DOCTYPE html>
<html lang="en">
<head>
<meta charset="utf-8">
<title>Brell Haulage Contracting – Business Cards</title>
<link href="https://fonts.googleapis.com/css2?family=Arimo:ital,wght@0,400;0,700;1,400;1,700&display=swap" rel="stylesheet">
<style>
  :root {
    --bg: #e6e3df;
    --paper: #ffffff;
    --red-light: #b71f2a;
    --red-dark: #8f171c;
    --brand-red: #cf1f2a;
    --ink: #333333;
    --ink-soft: #3d3d3d;
    --truck-top: #b9b9b9;
    --truck-bottom: #4a4a4a;
  }
  * { box-sizing: border-box; margin: 0; padding: 0; }
  html, body { width: 1200px; height: 1200px; overflow: hidden; }
  body {
    background: var(--bg);
    font-family: "Arimo", Arial, sans-serif;
    position: relative;
  }
  .card {
    position: absolute;
    width: 840px;
    height: 480px;
    background: var(--paper);
    box-shadow: 0 2px 6px rgba(0,0,0,0.15);
    overflow: hidden;
  }
  .card--back { left: 84px; top: 79px; }
  .card--front { left: 284px; top: 650px; }

  /* back card */
  .contact-panel {
    position: absolute;
    left: 463px; top: 0;
    width: 377px; height: 480px;
  }
  .name-band {
    height: 125px;
    background: var(--red-light);
    padding: 34px 0 0 50px;
    color: #fff;
  }
  .name-band .person-name { font-weight: 700; font-size: 31px; line-height: 1; }
  .name-band .person-title { font-size: 24px; letter-spacing: 2px; margin-top: 12px; line-height: 1; }
  .details-band {
    position: absolute;
    top: 131px; left: 0;
    width: 377px; height: 349px;
    background: var(--red-dark);
    padding: 52px 0 0 34px;
    color: #fff;
  }
  .contact-list { list-style: none; }
  .contact-list li {
    display: flex; align-items: center;
    font-size: 19px; line-height: 1;
    height: 33.5px;
  }
  .contact-list svg { width: 16px; height: 16px; margin-right: 9px; flex: none; fill: #fff; }
  .contact-list .email { font-size: 17px; }
  .postal {
    display: flex; margin-top: 38px;
    font-size: 21px; line-height: 28px;
  }
  .postal svg { width: 18px; height: 18px; margin: 2px 12px 0 0; fill: #fff; flex: none; }

  .truck-art {
    position: absolute;
    background: linear-gradient(to bottom, var(--truck-top), var(--truck-bottom));
    border-radius: 6px;
  }
  .card--back .truck-art { left: 32px; top: 45px; width: 396px; height: 320px; }
  .legal-line {
    position: absolute;
    right: 377px; margin-right: 29px;
    top: 406px;
    text-align: right;
    font-size: 19.5px; line-height: 30px;
    color: var(--ink);
    white-space: nowrap;
  }

  /* front card */
  .card--front .truck-art { left: 32px; top: 106px; width: 214px; height: 176px; }
  .brand-name {
    position: absolute;
    left: 286px; top: 124px;
    color: var(--brand-red);
    font-weight: 700;
    font-size: 62px;
    line-height: 60px;
    text-transform: uppercase;
  }
  .website {
    position: absolute;
    left: 286px; top: 338px;
    font-size: 27px;
    font-style: italic;
    letter-spacing: 2.5px;
    color: var(--ink-soft);
  }
  .website strong { color: var(--red-dark); }
</style>
</head>
<body>

<section class="card card--back">
  <div class="truck-art" role="img" aria-label="Grey illustration of a prime mover truck, front three-quarter view"></div>
  <p class="legal-line">Brell Holdings Pty Ltd (ACN 582 316 907)<br>ATF The Brell Discretionary Trust T/AS</p>

  <div class="contact-panel">
    <div class="name-band">
      <div class="person-name">Your Name</div>
      <div class="person-title">Title</div>
    </div>
    <div class="details-band">
      <ul class="contact-list">
        <li>
          <svg viewBox="0 0 16 16"><circle cx="8" cy="8" r="7" fill="none" stroke="#fff" stroke-width="1.5"/><path d="M5.5 4.5l1.6-.3.8 2-1 .8c.4 1 1.1 1.8 2.1 2.2l.8-1 2 .8-.3 1.6c-3 .4-6.3-2.9-6-6.1z"/></svg>
          08 9352 7140
        </li>
        <li class="email">
          <svg viewBox="0 0 16 16"><path d="M1 4h14v9H1z"/><path d="M1 4l7 5 7-5" fill="none" stroke="#8f171c" stroke-width="1.2"/></svg>
          brellhaul@mailbox-example.com.au
        </li>
        <li>
          <svg viewBox="0 0 16 16" fill="none" stroke="#fff" stroke-width="1.2"><circle cx="8" cy="8" r="6.5"/><ellipse cx="8" cy="8" rx="2.8" ry="6.5"/><path d="M1.5 8h13M2.5 5h11M2.5 11h11"/></svg>
          www.brellhaulage.com
        </li>
      </ul>
      <div class="postal">
        <svg viewBox="0 0 16 16"><path d="M8 1l7.5 7h-2.3v7H9.8v-4.5H6.2V15H2.8V8H.5z"/></svg>
        <span>P.O Box 817 Wattlegrove<br>WA, 6958</span>
      </div>
    </div>
  </div>
</section>

<section class="card card--front">
  <div class="truck-art" role="img" aria-label="Grey illustration of a prime mover truck"></div>
  <h1 class="brand-name">Brell<br>Haulage<br>Contracting</h1>
  <p class="website">www.<strong>brellhaulage</strong>.com</p>
</section>

</body>
</html>
```